Thornbury Spa

We are a large Miami Beach spa and salon. I am still building our website but you can use it as a resource to gain a better understanding of who we are ....www.velloraspa-studio.com.

We offer a comprehensive list of services in hair, nails, massage, skin care, tanning, spray tanning and waxing and we offer high quality products for skin care, tanning and hair. We are open 7 days.

We would like to see a clean and simple menu that looks a lot like the one from "The Spa at Larkwood." In particular, we have a copy of a menu from their West Hollywood, CA location that is just beautiful. In the uploaded content you will see a sampling of that menu. We would like to see greys, blacks, silvers, whites and warm colors like reds and oranges. We specifically attempt to remain gender neutral so that we don't attract only girls (with pink colors and flowers etc). The final design should convey a simple, clean, friendly environment and the final product should be sized such that it is 1.) portable and 2.) inexpensive to print. We will be running thousands of these at a time so cost of printing is a consideration.

The booklet consists of two parts: one part is the standard menu with descriptions of services and products and photos etc (think of this as the sales piece that convinces a potential customer to visit) and will be stapled together like you would expect a small menu to be and should resemble the Larkwood menu. The prices should not be included in this part of the booklet that will be printed and stapled. The other part is a single insert and is removable and replaceable. I want this removable insert placed in the last page of the book in a folder pocket or something else that you can think of so that when it's time to change prices here that I am not throwing away all of the booklets....I am only replacing the inserts at the end of the menu booklet. Please design this single page insert so that should a customer remove it from the booklet and keep it, that it stands alone with our name, logo, website and phone number. This page can and probably will have to be 2 sided.

At the back of the booklet, I also want the polices to be printed in one page (think fine print in any sort of business dealing.)

With regard to the look and feel slider of economical v upmarket...we definitely want to convey we deliver upmarket services at reasonable prices. Think, world class services and products at reasonable, everyday prices.

With regard to the uploaded files:
I uploaded both EPS and TIF formats. The colors in those files are not the palette we want at all. The colors we want use for the circular logo must match the standard colors as depicted in the uploaded file "Thornburytanrooms"

Target Market(s)

The target market is the average 20-35 year old in Miami Beach that cares about their appearance. The range of clientele is quite diverse.

Industry/Entity Type

Environment

Requirements
Must have
• It must have elegant and simple photographs that relate to the services being offered. We are selling a service set and an environment...so this menu should be reflect that goal. The logo should be repeated often throughout the book but in subtle ways.

Stock photos are fine as long as they don't seem obviously stock.

Should not have
• Nothing buddha like. Nothing themed. It should be all inclusive and not seek to identify with any particular group or gender.

Nothing that fits the stereotype of "Miami Beach." We want to represent ourselves in the same category as the best spas in the world because we moving everything we do in that direction. Think class!

```html
<!DOCTYPE html>
<html lang="en">
<head>
<meta charset="utf-8">
<title>Thornbury Spa — Hair Price Insert</title>
<link href="https://fonts.googleapis.com/css2?family=PT+Sans:wght@400;700&display=swap" rel="stylesheet">
<style>
  :root {
    --paper: #ffffff;
    --photo-light: #e2dcd6;
    --photo-warm: #c8a58d;
    --panel-text: #f4ece6;
    --frame-line: rgba(255, 255, 255, 0.55);
    --band: rgba(235, 235, 235, 0.78);
    --band-title: #5b5b5b;
    --band-copy: #2a2a2a;
    --brand-tan: #cdb99a;
  }
  html, body {
    margin: 0;
    padding: 0;
    overflow: hidden;
    background: var(--paper);
  }
  .spread {
    position: relative;
    width: 1200px;
    height: 600px;
    overflow: hidden;
    font-family: "PT Sans", sans-serif;
    background: var(--paper);
  }
  .hero-photo {
    position: absolute;
    left: 0; top: 0;
    width: 680px; height: 600px;
    background: linear-gradient(180deg, var(--photo-light) 0%, var(--photo-warm) 100%);
  }
  .title-band {
    position: absolute;
    left: 0; top: 431px;
    width: 680px; height: 104px;
    background: var(--band);
  }
  .title-band h1 {
    position: absolute;
    left: 49px; top: 33px;
    margin: 0;
    font-weight: 400;
    font-size: 42px;
    line-height: 1;
    letter-spacing: 12px;
    color: var(--band-title);
  }
  .title-band p {
    position: absolute;
    left: 210px; top: 33px;
    width: 380px;
    margin: 0;
    font-size: 8.6px;
    font-weight: 700;
    line-height: 11.5px;
    letter-spacing: 0.9px;
    color: var(--band-copy);
    white-space: nowrap;
  }
  .panel {
    position: absolute;
    left: 0; top: 0;
    width: 1200px; height: 600px;
  }
  .frame {
    position: absolute;
    left: 18px; top: 19px;
    width: 1163px; height: 559px;
    border: 1px solid var(--frame-line);
    box-sizing: border-box;
  }
  .price-list {
    position: absolute;
    left: 705px; top: 64px;
    width: 450px;
    color: var(--panel-text);
  }
  .price-row {
    display: grid;
    grid-template-columns: 262px 72px 1fr;
    font-size: 9.4px;
    line-height: 14.6px;
    height: 14.6px;
  }
  .price-row.heading {
    font-size: 12.2px;
    line-height: 16px;
    height: 16px;
    text-transform: uppercase;
    margin-top: 13px;
  }
  .price-row.heading.first { margin-top: 0; }
  .price-row.col-heads { text-transform: none; }
  .price-row.col-heads span:first-child { text-transform: uppercase; }
  .price-row .none { padding-left: 12px; }
  .brand {
    position: absolute;
    left: 994px; top: 515px;
    width: 200px;
    text-align: center;
    color: var(--brand-tan);
  }
  .brand-dot {
    display: block;
    width: 30px; height: 30px;
    margin: 0 auto 6px;
    border: 1.5px solid var(--brand-tan);
    border-radius: 50%;
    box-sizing: border-box;
  }
  .brand-name {
    font-size: 15px;
    font-weight: 400;
    letter-spacing: 2px;
    text-transform: uppercase;
    line-height: 1;
  }
</style>
</head>
<body>
<main class="spread">
  <div class="hero-photo" role="img" aria-label="Photograph of a guest relaxing on a white towel while receiving a scalp massage"></div>

  <section class="title-band">
    <h1>HAIR</h1>
    <p>Tina, conves conduc ta Simis sus, portis, eo esilicie mei potidees?<br>Arbessules curnihil hacchil lesigiti clum et vit; nicaella ponloctur. Imo<br>in tam poste, quam iam re confit. Ego publicesse te mac tenihil labul-<br>tus ompred senam adhus.</p>
  </section>

  <svg class="panel" width="1200" height="600" viewBox="0 0 1200 600" aria-hidden="true">
    <defs>
      <linearGradient id="panelTone" x1="0" y1="0" x2="1" y2="1">
        <stop offset="0" stop-color="#6a2b22"/>
        <stop offset="0.6" stop-color="#652d20"/>
        <stop offset="1" stop-color="#603718"/>
      </linearGradient>
    </defs>
    <path d="M664 0 H1200 V600 H552 Q664 585 664 416 Z" fill="url(#panelTone)"/>
  </svg>

  <div class="frame"></div>

  <section class="price-list">
    <div class="price-row heading first col-heads"><span>Hair</span><span>Residents</span><span>Hotel Guests</span></div>
    <div class="price-row heading col-heads"><span>Consultations</span><span>Always Free</span><span>Always Free</span></div>

    <div class="price-row heading"><span>Cutting</span><span></span><span></span></div>
    <div class="price-row"><span>Men’s Hair Cut</span><span>from $29</span><span>from $35</span></div>
    <div class="price-row"><span>Women’s Wet Cut</span><span>from $49</span><span>from $60</span></div>
    <div class="price-row"><span>Women’s Cut &amp; Blowout</span><span>from $69</span><span>from $80</span></div>

    <div class="price-row heading"><span>Styling</span><span></span><span></span></div>
    <div class="price-row"><span>Wet Head Blowout</span><span>from $25</span><span>from $30</span></div>
    <div class="price-row"><span>Shampoo &amp; Blowout</span><span>from $35</span><span>from $40</span></div>
    <div class="price-row"><span>Updos or Styling</span><span>from $49</span><span>from $80</span></div>
    <div class="price-row"><span>Wedding Hair Trials</span><span>from $89</span><span class="none">-</span></div>
    <div class="price-row"><span>Wedding Day Hair</span><span>from $49</span><span class="none">-</span></div>

    <div class="price-row heading"><span>Coloring</span><span></span><span></span></div>
    <div class="price-row"><span>Single Process</span><span>from $55</span><span>from $65</span></div>
    <div class="price-row"><span>Partial Highlights/Lowlights</span><span>from $99</span><span>from $120</span></div>
    <div class="price-row"><span>Full Highlights/Lowlights</span><span>from $149</span><span>from $180</span></div>
    <div class="price-row"><span>Double Process</span><span>from $99</span><span>from $110</span></div>

    <div class="price-row heading"><span>Treatments</span><span></span><span></span></div>
    <div class="price-row"><span>Scalp Massage + Nourishing Treatment</span><span>from $19</span><span>from $25</span></div>
    <div class="price-row"><span>Ultra Conditioning Reconstructor</span><span>from $29</span><span>from $35</span></div>
    <div class="price-row"><span>Keratin by Marisol treatment</span><span>from $199</span><span>from $250</span></div>

    <div class="price-row heading"><span>Extensions</span><span></span><span></span></div>
    <div class="price-row"><span>Hair Extensions by Lumenlocks</span><span>from $799</span><span>from $950</span></div>
    <div class="price-row"><span>Extensions Repair</span><span>from $249</span><span>from $300</span></div>
    <div class="price-row"><span>Extensions Removal</span><span>from $59</span><span>from $70</span></div>
  </section>

  <div class="brand">
    <span class="brand-dot"></span>
    <div class="brand-name">Thornbury Spa</div>
  </div>
</main>
</body>
</html>
```